Human Resource Consulting practice needs a business card design

We need a business card design (double sided colour) for our Human Resource (HR) consulting practice in regional New South Wales, australia. Our business name is Staff Compass. We support small and medium business across the Mid North Coast of New South Wales by providing them with outsourced HR support, services and products to help them achieve compliance with workplace legislation and across all areas of the employment lifecycle from recruitment to termination and everything in between. Our corporate colours are hot pink and black. The final design should communicate professionalism, trust, people focus.
I have attached the current (old) business card for your reference.

Target Market(s)

Business owners and high level managers

Industry/Entity Type

Business

Contact Information for Business Card

Name
Title
Phone no
Mobile no
Address
PO Box
email address
website

Colors
e34197

Requirements
Must have
• Tempate for changing business card personal details including Name, position title, mobile number, email address.
• Keep current logo and colours as per attached
• Logo must be presented in 2 colours or black only not white
Nice to have
• One side logo and graphic only other side logo and personal details
Should not have
• Should not be the same as the current version (attached) but a modern interpretation.
• Does not need a busy reverse side with our list of services as per current version. I feel this is too busy.
• No photos

```html
<!DOCTYPE html>
<html lang="en">
<head>
<meta charset="utf-8">
<title>Staff Compass – Business Card</title>
<link rel="stylesheet" href="https://fonts.googleapis.com/css2?family=Lato:wght@400;700;900&display=swap">
<style>
  :root {
    --hot-pink: #e34197;
    --pink-light: #f06cbd;
    --pink-deep: #d8338a;
    --ink: #151315;
    --ink-soft: #2a262a;
    --grey-text: #4a4a4a;
    --paper: #ffffff;
    --backdrop: #ece9e4;
    --star-grey: #3b363b;
  }
  * { box-sizing: border-box; margin: 0; padding: 0; }
  html, body { width: 1200px; height: 1023px; overflow: hidden; }
  body {
    background: var(--backdrop);
    font-family: "Lato", Arial, sans-serif;
    position: relative;
  }
  .card {
    position: absolute;
    width: 600px;
    height: 343px;
    border-radius: 22px;
    overflow: hidden;
    box-shadow: 0 10px 28px rgba(0,0,0,.18);
  }

  /* Front */
  .card-front { left: 60px; top: 90px; background: var(--paper); }
  .brand {
    position: absolute;
    left: 40px; top: 44px;
    display: flex; align-items: center; gap: 12px;
  }
  .brand-dot { width: 14px; height: 14px; border-radius: 50%; background: var(--hot-pink); }
  .brand-name { font-weight: 900; font-size: 40px; color: var(--hot-pink); letter-spacing: -0.5px; }
  .person { position: absolute; left: 40px; top: 124px; }
  .person-name { font-weight: 700; font-size: 19px; color: var(--hot-pink); }
  .person-title { font-size: 16px; color: var(--grey-text); margin-top: 4px; }

  .contact-band {
    position: absolute;
    left: 0; right: 0; bottom: 0; height: 150px;
    background: linear-gradient(90deg, var(--pink-light), var(--hot-pink) 60%, var(--pink-deep));
  }
  .band-graphic {
    position: absolute;
    right: 36px; top: 132px;
    width: 130px; height: 90px;
    background: linear-gradient(135deg, var(--pink-light), var(--hot-pink));
    border-radius: 6px;
  }
  .contact-list {
    position: absolute; left: 40px; bottom: 22px;
    list-style: none;
  }
  .contact-list li {
    display: flex; align-items: center; gap: 10px;
    color: var(--paper); font-size: 15.5px; line-height: 26px;
  }
  .contact-list svg { width: 15px; height: 15px; flex: none; }
  .postal {
    position: absolute; right: 40px; bottom: 48px;
    color: var(--paper); font-size: 15.5px; line-height: 24px; text-align: right;
  }

  /* Back */
  .card-back {
    left: 540px; top: 560px;
    background: linear-gradient(160deg, var(--ink-soft), var(--ink) 55%);
  }
  .back-pattern {
    position: absolute; left: 0; top: 0; bottom: 0; width: 58%;
    background: linear-gradient(90deg, rgba(90,82,90,.45), rgba(60,54,60,.15) 80%, transparent);
  }
  .back-brand {
    position: absolute; right: 48px; top: 50%;
    transform: translateY(-50%);
    display: flex; align-items: center; gap: 14px;
  }
  .back-brand .brand-dot { width: 18px; height: 18px; }
  .back-brand .brand-name { font-size: 46px; }
</style>
</head>
<body>

<section class="card card-front" aria-label="Business card front">
  <div class="brand">
    <span class="brand-dot"></span>
    <span class="brand-name">Staff Compass</span>
  </div>
  <div class="person">
    <p class="person-name">Claire Moreton</p>
    <p class="person-title">Principal Consultant</p>
  </div>

  <div class="contact-band"></div>
  <div class="band-graphic" role="img" aria-label="Large pink star graphic rising from the contact band"></div>

  <ul class="contact-list">
    <li>
      <svg viewBox="0 0 16 16" fill="#fff"><path d="M3 1h3l1.5 4-2 1.2a9 9 0 0 0 4.3 4.3L11 8.5l4 1.5v3a2 2 0 0 1-2 2A12 12 0 0 1 1 3a2 2 0 0 1 2-2z"/></svg>
      02 6500 1234
    </li>
    <li>
      <svg viewBox="0 0 16 16" fill="none" stroke="#fff" stroke-width="1.6"><rect x="4" y="1" width="8" height="14" rx="1.5"/><circle cx="8" cy="12.5" r=".6" fill="#fff"/></svg>
      0400 555 210
    </li>
    <li>
      <svg viewBox="0 0 16 16" fill="none" stroke="#fff" stroke-width="1.6"><rect x="1" y="3" width="14" height="10" rx="1"/><path d="M1 3l7 6 7-6"/></svg>
      claire@staffcompass.com.au
    </li>
    <li>
      <svg viewBox="0 0 16 16" fill="none" stroke="#fff" stroke-width="1.4"><circle cx="8" cy="8" r="6.5"/><ellipse cx="8" cy="8" rx="3" ry="6.5"/><path d="M1.5 8h13M3 4.5h10M3 11.5h10"/></svg>
      www.staffcompass.com.au
    </li>
  </ul>

  <p class="postal">P.O. Box 120<br>Harbour Point<br>NSW 2400</p>
</section>

<section class="card card-back" aria-label="Business card back">
  <div class="back-pattern" role="img" aria-label="Faint grey star pattern across the dark background"></div>
  <div class="back-brand">
    <span class="brand-dot"></span>
    <span class="brand-name">Staff Compass</span>
  </div>
</section>

</body>
</html>
```